Stationary for a manufacturing company
Osmira Professional Wear
Stationary for a manufacturing company - Manufacturing
Creative Brief
Simple
John Doe
VP Sales and Marketing
123 Street Name, City Country Zip Code
example@email.com
www.example.com
Font: Hug me Tight and Neuropol Osmira is a brand that creates professional uniforms- chefs, corporate, and etc Business card and stationary designs are up to the designers. My only comments are to make the business card: 1.) Easy to read 2.) Professional looking 3.) Clean I have uploaded photos of the logo and the shade of red used Logo should also appear in the front of the card. Also, no need to limit yourself in using the same font as the logo. Feel free to use other fonts
Use logo uploaded (side icon, red background). Red Background. Shade of red will be provided in the uploads.
sodrk sodrk
Designers Please add the company name on top of the address or wherever you think it will fit. For now, please use "Example Company, Inc."

```html
<!DOCTYPE html>
<html lang="en">
<head>
<meta charset="utf-8">
<title>Osmira Professional Wear — Business Card</title>
<link href="https://fonts.googleapis.com/css2?family=Quicksand:wght@400;500;700&family=Arimo:wght@400&display=swap" rel="stylesheet">
<style>
  :root {
    --stage: #000000;
    --brand-red: #a81a0b;
    --paper: #ffffff;
    --label: #ffffff;
    --ink-light: #f3e3e0;
  }
  * { margin: 0; padding: 0; box-sizing: border-box; }
  html, body { width: 1200px; height: 828px; overflow: hidden; background: var(--stage); }
  .canvas { position: relative; width: 1200px; height: 828px; font-family: "Quicksand", sans-serif; }

  .card { position: absolute; top: 250px; width: 475px; height: 268px; overflow: hidden; }
  .card--front { left: 115px; background: var(--brand-red); color: var(--paper); }
  .card--back { left: 610px; background: var(--paper); }

  .side-label {
    position: absolute; top: 540px; width: 200px; text-align: center;
    font-family: "Arimo", sans-serif; font-size: 38px; color: var(--label);
  }
  .side-label--front { left: 267px; }
  .side-label--back { left: 807px; }

  /* front */
  .brand { position: absolute; left: 32px; top: 78px; width: 160px; text-align: center; }
  .brand__dot { display: block; width: 52px; height: 52px; border-radius: 50%; background: var(--paper); margin: 0 auto 8px; }
  .brand__name { font-weight: 700; font-size: 38px; letter-spacing: 1px; line-height: 1; }
  .divider { position: absolute; left: 221px; top: 62px; width: 2px; height: 180px; background: var(--paper); }
  .person { position: absolute; left: 238px; top: 66px; }
  .person__name { font-weight: 500; font-size: 22px; line-height: 1; }
  .person__title { font-size: 10px; margin-top: 4px; }
  .contacts { position: absolute; left: 238px; top: 120px; list-style: none; }
  .contacts li { display: flex; align-items: center; height: 20px; font-size: 9.5px; font-weight: 500; color: var(--ink-light); }
  .contacts svg { width: 10px; height: 10px; margin-right: 6px; flex: none; }

  /* back */
  .back-shape { position: absolute; left: 0; top: 0; }
  .web-mark { position: absolute; left: 300px; top: 122px; display: flex; align-items: center; color: var(--brand-red); }
  .web-mark__dot { width: 18px; height: 18px; border-radius: 50%; background: var(--brand-red); margin-right: 5px; }
  .web-mark__name { font-weight: 700; font-size: 19px; }
</style>
</head>
<body>
<div class="canvas">

  <section class="card card--front">
    <div class="brand">
      <span class="brand__dot"></span>
      <div class="brand__name">Osmira</div>
    </div>
    <div class="divider"></div>
    <div class="person">
      <div class="person__name">John Doe</div>
      <div class="person__title">VP Sales and Marketing</div>
    </div>
    <ul class="contacts">
      <li><svg viewBox="0 0 10 10"><circle cx="5" cy="5" r="5" fill="#fff"/><path d="M5 2.2a1.8 1.8 0 0 0-1.8 1.8c0 1.4 1.8 3.6 1.8 3.6s1.8-2.2 1.8-3.6A1.8 1.8 0 0 0 5 2.2z" fill="#a81a0b"/></svg>123 Street Name, City Country 12345</li>
      <li><svg viewBox="0 0 10 10"><circle cx="5" cy="5" r="5" fill="#fff"/><path d="M3.3 2.5l1 1-.5.8a4 4 0 0 0 1.9 1.9l.8-.5 1 1-.7.8C5 7.3 2.7 5 2.5 3.2z" fill="#a81a0b"/></svg>+1(617)555-0186</li>
      <li><svg viewBox="0 0 10 10"><circle cx="5" cy="5" r="5" fill="#fff"/><path d="M3.3 2.5l1 1-.5.8a4 4 0 0 0 1.9 1.9l.8-.5 1 1-.7.8C5 7.3 2.7 5 2.5 3.2z" fill="#a81a0b"/></svg>+1(617)555-0142</li>
      <li><svg viewBox="0 0 10 10"><circle cx="5" cy="5" r="5" fill="#fff"/><rect x="3" y="2.5" width="4" height="5" fill="#a81a0b"/></svg>+1(617)555-0197</li>
      <li><svg viewBox="0 0 10 10"><circle cx="5" cy="5" r="5" fill="#fff"/><rect x="2.5" y="3.3" width="5" height="3.4" fill="#a81a0b"/></svg>example@email.com</li>
    </ul>
  </section>

  <section class="card card--back">
    <svg class="back-shape" width="475" height="268" viewBox="0 0 475 268">
      <path d="M0 0H182C95 40 32 150 20 268H0Z" fill="var(--brand-red)"/>
    </svg>
    <div class="web-mark">
      <span class="web-mark__dot"></span>
      <span class="web-mark__name">Osmira.com</span>
    </div>
  </section>

  <div class="side-label side-label--front">font</div>
  <div class="side-label side-label--back">back</div>

</div>
</body>
</html>
```